Business cards for Norwegian software consultancy business

We are in need of business cards for our Norwegian consultancy company.
“Valto Brindex AS” specializes in software development, architecture and agile methodology, providing mostly on-site services at customers.
The cards should reflect a certain level of business professionalism with an elegant touch, while paying tribute to our modern and technological heritage. Our logo should be featured, as well as room for basic information about the cardholder and legal information of the company (company name, address and VAT number).
We would like our cards to reflect that we are a modern consulting company. It should present a professional image that people will remember. The texture and color pallette should reflect our professionalism and reliability, so we prefer a light color pallette with colors such as gray, white, blue and black. The number of colors used should however not be overwhelming, with the text being distinct and readable.
We are open to untraditional layouts and playful designs as long as they communicate the intent stated above.
You could also take a look at our website http://www.brindex.no for input on our visual profile.
Our logo is attached in the form of vectors and rasterized PNG. Please comment if you would like the black-white and/or inverted versions as well.
Industry/Entity Type
Architecture
Contact Information for Business Card
Company information:
Valto Brindex AS
Kvernlia 14, 3170 Sem
482 71 519
info@brindex.no
www.brindex.no
Employee information:
Full name
Title
Email
Phone
Font styles to use
Look and feel

```html
<!DOCTYPE html>
<html lang="no">
<head>
<meta charset="utf-8">
<title>Valto Brindex AS – Business Cards</title>
<link rel="stylesheet" href="https://fonts.googleapis.com/css2?family=Open+Sans:wght@400;600;700&display=swap">
<style>
  :root {
    --page-bg: #e8e4de;
    --brand-blue: #529fd6;
    --ink: #141414;
    --paper: #ffffff;
    --rule: #2a2a2a;
  }
  * { box-sizing: border-box; margin: 0; padding: 0; }
  html, body {
    width: 1200px; height: 749px; overflow: hidden;
    background: var(--page-bg);
    font-family: "Open Sans", Arial, sans-serif;
  }
  .canvas { position: relative; width: 1200px; height: 749px; }

  .card {
    position: absolute; top: 200px; width: 545px; height: 309px;
    overflow: hidden;
    box-shadow: 0 18px 28px rgba(0,0,0,.18);
  }
  .card--front { left: 39px; background: var(--brand-blue); }
  .card--back  { left: 621px; background: var(--paper); }

  .wordmark {
    position: absolute; display: flex; align-items: center;
    font-weight: 600; letter-spacing: .04em; white-space: nowrap;
  }
  .wordmark__square { display: inline-block; }
  .card--front .wordmark { left: 27px; top: 228px; color: var(--paper); font-size: 26px; gap: 12px; }
  .card--front .wordmark__square { width: 26px; height: 26px; background: var(--paper); }
  .card--back .wordmark { left: 27px; top: 38px; color: var(--ink); font-size: 40px; gap: 18px; }
  .card--back .wordmark__square { width: 40px; height: 40px; background: var(--brand-blue); }

  .holder-name {
    position: absolute; right: 27px; top: 151px;
    color: var(--brand-blue); font-weight: 700; font-size: 14px;
  }
  .holder-rule {
    position: absolute; left: 27px; top: 181px; width: 439px; height: 1px;
    background: var(--rule);
  }
  .holder-title {
    position: absolute; right: 27px; top: 171px;
    color: var(--ink); font-size: 12.5px;
  }
  .edge-tab {
    position: absolute; right: 0; top: 155px; width: 11px; height: 30px;
    background: var(--brand-blue);
  }

  .company-address {
    position: absolute; left: 27px; top: 236px;
    color: var(--ink); font-size: 13px; line-height: 17px;
  }
  .contact-list {
    position: absolute; right: 27px; top: 222px;
    list-style: none; color: var(--ink); font-size: 12.5px; line-height: 16px; text-align: right;
  }
  .contact-list li { display: flex; justify-content: flex-end; align-items: center; gap: 5px; }
  .contact-list svg { width: 11px; height: 11px; fill: var(--brand-blue); }

  .foot-band { position: absolute; top: 286px; height: 23px; }
  .foot-band--dark { left: 0; width: 270px; background: var(--ink); }
  .foot-band--blue { left: 274px; right: 0; background: var(--brand-blue); }
</style>
</head>
<body>
<main class="canvas">

  <section class="card card--front" aria-label="Card front">
    <div class="wordmark"><span class="wordmark__square"></span>VALTO BRINDEX</div>
  </section>

  <section class="card card--back" aria-label="Card back">
    <div class="wordmark"><span class="wordmark__square"></span>VALTO BRINDEX</div>

    <p class="holder-name">Lars Hovland</p>
    <div class="holder-rule"></div>
    <p class="holder-title">Manger</p>
    <div class="edge-tab"></div>

    <p class="company-address">Valto Brindex AS Kvernlia<br>14, 3170 Sem 482 71 519</p>

    <ul class="contact-list">
      <li>+ 47 913 52 608
        <svg viewBox="0 0 12 12" aria-hidden="true"><path d="M1 5c0-2 2-3.5 5-3.5S11 3 11 5H8.5V3.8h-5V5zM2.5 6h7l1 4.5h-9z"/></svg>
      </li>
      <li>info@brindex.no
        <svg viewBox="0 0 12 12" aria-hidden="true"><path d="M0.5 2.5h11v7h-11zM1.5 3.3 6 6.6l4.5-3.3z" fill-rule="evenodd"/></svg>
      </li>
      <li>www.brindex.no
        <svg viewBox="0 0 12 12" aria-hidden="true"><circle cx="6" cy="6" r="5.5"/><path d="M0.5 6h11M6 .5c-2 2-2 9 0 11M6 .5c2 2 2 9 0 11" stroke="#fff" stroke-width=".8" fill="none"/></svg>
      </li>
    </ul>

    <div class="foot-band foot-band--dark"></div>
    <div class="foot-band foot-band--blue"></div>
  </section>

</main>
</body>
</html>
```